Overseas Property Tax Depreciation

We need a two sided flyer to promote our business and explain what we do. our website is www.dorwix.net.
The attached word file is what I would like on an A5 size flyer with one side showing the FAQ and the other the worked example. I would like these formatted much better than the are and in general style of the website. I will attach files for logos as well.

```html
<!DOCTYPE html>
<html lang="en">
<head>
<meta charset="utf-8">
<title>Overseas Property Tax Depreciation</title>
<link href="https://fonts.googleapis.com/css2?family=Arimo:ital,wght@0,400;0,700;1,700&display=swap" rel="stylesheet">
<style>
:root{
  --navy:#0f2a5c;
  --bar:#a9d1ee;
  --bar-edge:#7fb4de;
  --ink:#1b1f2a;
  --paper:rgba(255,255,255,.93);
  --photo-a:#5b7fa6;
  --photo-b:#c9d6e3;
  --photo-c:#2d4f78;
  --tick:#1a7a3a;
}
*{box-sizing:border-box;margin:0;padding:0}
html,body{width:863px;height:1200px;overflow:hidden}
body{font-family:"Arimo",Arial,sans-serif;color:var(--ink);position:relative}
.backdrop{position:absolute;inset:0;background:linear-gradient(160deg,var(--photo-b) 0%,var(--photo-a) 35%,var(--photo-c) 70%,var(--photo-a) 100%)}
.brand{position:absolute;top:14px;right:18px;width:140px;height:70px;background:#fff;display:flex;align-items:center;justify-content:center;gap:8px;padding:0 8px}
.brand-dot{width:22px;height:22px;border-radius:50%;background:var(--navy);flex:none}
.brand-name{font-weight:700;font-size:13px;color:var(--navy);line-height:1.1}
.content{position:absolute;left:30px;right:30px;top:98px;bottom:238px}
.section{margin-bottom:8px}
.heading{background:linear-gradient(var(--bar),var(--bar-edge));color:var(--navy);font-style:italic;font-weight:700;font-size:15px;padding:4px 10px;display:inline-block;min-width:300px;border-radius:2px}
.heading.wide{display:block;font-size:14.5px;line-height:1.2}
.body{background:var(--paper);font-size:10.6px;line-height:1.38;padding:6px 10px;margin-top:2px}
.body p+p{margin-top:4px}
.body ul{margin:3px 0 0 18px}
.ticks{list-style:none;margin:4px 0 0 4px}
.ticks li{display:flex;align-items:center;gap:6px;margin:2px 0}
.photo-bottom{position:absolute;left:0;right:0;bottom:0;height:230px;background:linear-gradient(180deg,var(--photo-c),var(--photo-a) 60%,#7c9a5f)}
</style>
</head>
<body>
<div class="backdrop" role="img" aria-label="Photo of tax forms, calculator and papers in blue tones"></div>

<div class="brand"><span class="brand-dot"></span><span class="brand-name">Meridian<br>Surveyors Guild</span></div>

<main class="content">
  <section class="section">
    <h2 class="heading">Why use us?</h2>
    <div class="body">
      <p>There are several websites out there offering tax depreciation reports for Australian properties but there are very few who are appropriately qualified and approved by the National Revenue Office (NRO) and offer the necessary Irish expertise. The Quantity Surveyor that prepares your report:</p>
      <ul>
        <li>is Irish and qualified as a Quantity Surveyor in Ireland.</li>
        <li>worked there during the "Celtic Tiger" period when construction costs were quite high.</li>
        <li>has detailed knowledge of Irish construction methods and costs over the past 20 years. Irish buildings are generally much more expensive than Australian due to the climate, just think about how many Australian houses you have seen that have double glazing, central heating, insulation etc.,</li>
        <li>has a partnership arrangement with an Irish quantity surveying firm to carry out the property inspections required in most cases to maximise the deductions available.</li>
        <li>is a chartered member of the Guild.</li>
        <li>Maintains the Appropriate Professional Indemnity Insurance.</li>
        <li>is registered with the Tax Agents Council. All quantity surveyors who prepare Property Tax Depreciation Schedules are required by the NRO to be registered with the Tax Agents Council to ensure they have checked that the person preparing the report is suitably qualified and maintains the appropriate professional indemnity insurance. You can check the registration on the TAC register.</li>
        <li>Our registration number is 24815377.</li>
      </ul>
    </div>
  </section>

  <section class="section">
    <h2 class="heading">My property is in Ireland does this make a difference?</h2>
    <div class="body">
      <p>Division 43 of the Income Tax Assessment Act 1997 which deals with capital works depreciation states that it applies to buildings begun outside Australia after 21 August 1990 Sect 43.20 (1) (b). Your Australian tax return should cover your worldwide income. As long as the property is available to rent back in Ireland you are obliged by the NRO to report any income or loss on that property.</p>
    </div>
  </section>

  <section class="section">
    <h2 class="heading">Is my property too old?</h2>
    <div class="body">
      <p>No, if your property was constructed after 1990 you can claim for both the construction cost element and the Plant and equipment. If it was built before then you can still claim the plant and equipment allowance. The easiest thing to do is to contact us with some details on your property and we can make an initial assessment of the possible annual savings.</p>
    </div>
  </section>

  <section class="section">
    <h2 class="heading">What is Property Depreciation?</h2>
    <div class="body">
      <p>Just like you claim wear and tear on a car purchased for income producing purposes, you can also claim the depreciation of your investment property against your taxable income.</p>
      <p>There are 2 types available; depreciation on Plant and Equipment, and depreciation on the cost of construction. Plant and Equipment refers to items within the building like ovens, dishwashers, carpet and blinds etc. Both these costs can be offset against your assessable income.</p>
    </div>
  </section>

  <section class="section">
    <h2 class="heading">How much will the report cost?</h2>
    <div class="body">
      <p>Each scenario is different so contact us to obtain a quick quote for your situation. Generally the cost of the report is a fraction of the savings in any one year.</p>
      <ul class="ticks">
        <li><svg width="12" height="12" viewBox="0 0 12 12"><path d="M1 6l3 3 7-7" fill="none" stroke="var(--tick)" stroke-width="2"/></svg>Our fee is fully tax deductible</li>
        <li><svg width="12" height="12" viewBox="0 0 12 12"><path d="M1 6l3 3 7-7" fill="none" stroke="var(--tick)" stroke-width="2"/></svg>You do NOT need to get this report done every year so the cost can be spread over several years</li>
      </ul>
    </div>
  </section>

  <section class="section">
    <h2 class="heading wide">I haven't included my property for the past couple of years on my tax return is this a problem?</h2>
    <div class="body">
      <p>No, in actual fact you could have been missing out on savings for a number of years, you can also use this report to claim a refund from the NRO for up to the past three years.</p>
    </div>
  </section>
</main>

<div class="photo-bottom" role="img" aria-label="Photo of banknotes and coins"></div>
</body>
</html>
```